MRT Property - Business Cards

Looking for a business card & general letterhead, signage etc design for our new logo.

Colours:
000a20
0056a2
00b5ef
0088ce
68cef2

Fonts:
Poppins
Karla

Please keep look and feel of new brand - example in the zip package I sent.

```html
<!DOCTYPE html>
<html lang="en">
<head>
<meta charset="utf-8">
<title>MRT Property – Business Cards</title>
<link rel="stylesheet" href="https://fonts.googleapis.com/css2?family=Poppins:wght@400;600;700&family=Karla:wght@400;500&display=swap">
<style>
  :root {
    --navy: #000a20;
    --royal: #0056a2;
    --sky: #00b5ef;
    --azure: #0088ce;
    --ice: #68cef2;
    --white: #ffffff;
    --stage: #3f3f3f;
  }
  html, body {
    margin: 0;
    width: 1200px;
    height: 803px;
    overflow: hidden;
    background: var(--stage);
  }
  .sheet {
    position: relative;
    width: 1200px;
    height: 803px;
  }
  .card {
    position: absolute;
    top: 256px;
    width: 500px;
    height: 290px;
    border-radius: 18px;
    overflow: hidden;
    box-shadow: 0 14px 30px rgba(0, 0, 0, 0.45);
  }
  .card--front { left: 70px; background: var(--white); }
  .card--back { left: 630px; background: var(--azure); }

  .front-shapes {
    position: absolute;
    inset: 0;
  }
  .holder {
    position: absolute;
    left: 34px;
    top: 44px;
    color: var(--white);
    font-family: "Karla", sans-serif;
  }
  .holder__name {
    margin: 0;
    font-family: "Poppins", sans-serif;
    font-weight: 700;
    font-size: 21px;
    line-height: 1.1;
  }
  .holder__role {
    margin: 2px 0 0;
    font-size: 12px;
  }
  .holder__address {
    margin: 28px 0 8px;
    font-style: normal;
    font-size: 12.5px;
    line-height: 1.3;
  }
  .contact-list {
    list-style: none;
    margin: 0;
    padding: 0;
    font-size: 12.5px;
    line-height: 1.35;
  }
  .contact-list li {
    display: flex;
    align-items: center;
    gap: 8px;
  }
  .contact-list svg { width: 10px; height: 10px; flex: none; }

  .brand {
    position: absolute;
    font-family: "Poppins", sans-serif;
    font-weight: 700;
    white-space: nowrap;
    display: flex;
    align-items: center;
    gap: 8px;
  }
  .brand__dot {
    border-radius: 50%;
    flex: none;
  }
  .brand--front {
    left: 290px;
    right: 10px;
    top: 78px;
    justify-content: center;
    font-size: 21px;
    line-height: 1;
    color: var(--royal);
  }
  .brand--front .brand__dot { width: 15px; height: 15px; background: var(--sky); }
  .brand--back {
    left: 50%;
    top: 50%;
    transform: translate(-50%, -50%);
    gap: 10px;
    font-size: 46px;
    color: var(--sky);
  }
  .brand--back .brand__dot { width: 30px; height: 30px; background: var(--royal); }
</style>
</head>
<body>
<main class="sheet">
  <section class="card card--front" aria-label="Business card front">
    <svg class="front-shapes" viewBox="0 0 500 290" preserveAspectRatio="none" aria-hidden="true">
      <path d="M0 0 H250 C215 60 208 200 262 290 H0 Z" fill="var(--royal)"/>
      <path d="M250 0 C215 60 208 200 262 290" fill="none" stroke="var(--sky)" stroke-width="7"/>
      <path d="M262 0 C228 70 222 200 276 290" fill="none" stroke="var(--royal)" stroke-width="2"/>
      <path d="M272 0 C240 70 235 200 288 290" fill="none" stroke="var(--ice)" stroke-width="1.5"/>
    </svg>
    <div class="holder">
      <h1 class="holder__name">Daniel Reyes</h1>
      <p class="holder__role">President</p>
      <address class="holder__address">214 Harbour View Road<br>Lakefield, Canada 20817</address>
      <ul class="contact-list">
        <li><svg viewBox="0 0 10 10"><path d="M2 1 L4 3 L3 4 C4 6 5 7 6 7 L7 6 L9 8 L8 9 C4 9 1 6 1 2 Z" fill="currentColor"/></svg>555-201-4876</li>
        <li><svg viewBox="0 0 10 10"><rect x="2.5" y="0.5" width="5" height="9" rx="1" fill="none" stroke="currentColor"/></svg>555-309-6142</li>
        <li><svg viewBox="0 0 10 10"><rect x="0.5" y="2" width="9" height="6" fill="none" stroke="currentColor"/><path d="M0.5 2 L5 5.5 L9.5 2" fill="none" stroke="currentColor"/></svg>info@mrtproperty.com</li>
        <li><svg viewBox="0 0 10 10"><circle cx="5" cy="5" r="4.3" fill="none" stroke="currentColor"/><path d="M0.7 5 H9.3 M5 0.7 C2.5 3 2.5 7 5 9.3 M5 0.7 C7.5 3 7.5 7 5 9.3" fill="none" stroke="currentColor" stroke-width="0.8"/></svg>www.mrtproperty.com</li>
      </ul>
    </div>
    <div class="brand brand--front"><span class="brand__dot"></span>MRT Property</div>
  </section>

  <section class="card card--back" aria-label="Business card back">
    <div class="brand brand--back"><span class="brand__dot"></span>MRT Property</div>
  </section>
</main>
</body>
</html>
```